Mortgage Protection Insurance Flyer

The target audience are new home owners so the design needs to be clean and simple.

This a primarily for Final Expense Insurance, but need an area where it says "We Also Specialize In:"
- Medicare Supplement Insurance (MediGap)
- Annuities
- Final Expense

All flyer versions need to be editable. Colors to be used are red, white or black. Refer to my website for colors and photos (corvantshield.com). Will attach my logo and a flyer that I found online that is the format that I am looking for (for 8.5 in. x 11 in version). Need flyer in standard letter size 8.5 in. x11 in. but also in 8.5 in. x 5.5 in and 5.0 in. x 8.0 in. All sizes to be portrait oriented. If picked as winning design, need all flyer versions in full color, also in grey scale and files in all industry file types.

Content can be taken from my website..... corvantshield.com

Do NOT submit if you are not willing to provide all versions as described above for the original project price.

Must use royalty-free stock photos please.

Target Market(s)

New homeowners looking for insurance to protect there mortgage payments

Industry/Entity Type

Life Insurance

Colors
f69fa3

Requirements
Must have
• Colors to be used are red, white or black.
• Need flyer in standard letter size 8.5 in. x11 in. but also in 3.5 in. x 8.5 in (Full Bleed 3.75 in by 8.75 in.) and 4.0 in. x 6.0 in. (Full Bleed 4.12 in x 6.12 in) Each design tailored to the size dimensions (So no squeezing 8.5 x 11 design into a 4.0 x 6.0 space.) All sizes to be portrait oriented. If picked as winning design, need all flyer versions in full color, also in grey scale and files in all file types.
• Do not need physical address on flyer, do need email address on flyer though - tkelwer@corvantshield.com
• So phone number should be prominent, email address and website address should also be contact area.
• If you can not agree to terms above, do not submit any designs.
• Need facebook & twitter logos somewhere in contact info area.
Nice to have
• See sample flyers I have attached.
• White background with red used as primary graphic color and black used as secondary graphic if needed.
• font to be used should similar to one used in logo.

```html
<!DOCTYPE html>
<html lang="en">
<head>
<meta charset="utf-8">
<title>Corvant Shield Insurance – Final Expense Flyer</title>
<link rel="stylesheet" href="https://fonts.googleapis.com/css2?family=Exo+2:ital,wght@0,800;1,800&family=Montserrat:wght@400;500;600;700;800&display=swap">
<style>
  :root {
    --red: #d9222e;
    --red-light: #e8434b;
    --ink: #2b2b2b;
    --text: #4a4a4a;
    --grey-dark: #4b4b4b;
    --footer: #262626;
    --paper: #f4f4f4;
    --canvas: #e6e6e6;
    --white: #ffffff;
  }
  * { margin: 0; padding: 0; box-sizing: border-box; }
  html, body { width: 1200px; height: 857px; overflow: hidden; }
  body {
    background: var(--canvas);
    font-family: "Montserrat", sans-serif;
    color: var(--text);
    position: relative;
  }
  .flyer {
    position: absolute;
    left: 294px; top: 20px;
    width: 612px; height: 816px;
    background: var(--paper);
    overflow: hidden;
    box-shadow: 0 2px 12px rgba(0,0,0,.18);
  }
  .hero-band {
    position: absolute; left: 0; top: 129px;
    width: 420px; height: 163px;
    background: linear-gradient(100deg, var(--red-light), var(--red));
  }
  .hero-art { position: absolute; left: 0; top: 0; width: 612px; height: 360px; }
  .brand {
    position: absolute; left: 31px; top: 66px;
    font-weight: 800; font-size: 23px; letter-spacing: -0.5px;
    color: var(--ink);
    display: flex; align-items: center; gap: 8px;
  }
  .brand-dot { width: 13px; height: 13px; background: var(--red); }
  .hero-title {
    position: absolute; left: 30px; top: 145px;
    font-family: "Exo 2", sans-serif; font-weight: 800; font-style: italic;
    font-size: 23px; line-height: 25px; color: var(--white);
  }
  .hero-lead {
    position: absolute; left: 30px; top: 208px; width: 226px;
    font-size: 10.4px; line-height: 13.6px; font-weight: 500; color: var(--white);
    text-align: left;
  }
  .col-left { position: absolute; left: 31px; top: 316px; width: 265px; }
  .col-right { position: absolute; left: 320px; top: 340px; width: 256px; }
  .section-title { color: var(--red); font-weight: 600; font-size: 12px; margin-bottom: 6px; }
  .about-title {
    color: var(--red); font-family: "Exo 2", sans-serif;
    font-weight: 800; font-size: 15px; margin-bottom: 9px;
  }
  .sub-title { color: var(--ink); font-weight: 600; font-size: 12px; margin-bottom: 3px; }
  p { font-size: 9.6px; line-height: 12.4px; text-align: justify; }
  .plain { text-align: left; }
  .benefits-title { color: var(--red); font-weight: 600; font-size: 12px; margin: 16px 0 4px; }
  .check-list { list-style: none; }
  .check-list li {
    position: relative; padding-left: 13px;
    font-size: 9.6px; line-height: 12.4px; margin-bottom: 6.2px; text-align: justify;
  }
  .check-list li::before {
    content: ""; position: absolute; left: 1px; top: 2.5px;
    width: 6px; height: 6px; border: 1.3px solid var(--red); border-radius: 1px;
  }
  .check-list li::after {
    content: ""; position: absolute; left: 3px; top: 3px;
    width: 2.5px; height: 4.5px; border-right: 1.4px solid var(--red);
    border-bottom: 1.4px solid var(--red); transform: rotate(40deg);
  }
  .right-list { margin: 6px 0 4px; }
  .right-list li { margin-bottom: 4.6px; }
  .block { margin-bottom: 18px; }
  .rates { position: absolute; left: 31px; top: 625px; width: 265px; }
  .rate-row { display: flex; gap: 2px; margin-bottom: 3px; height: 19px; }
  .rate-label {
    flex: 0 0 172px; background: var(--grey-dark); color: var(--white);
    font-size: 9.4px; line-height: 19px; padding-left: 11px;
  }
  .rate-value {
    flex: 1; background: var(--red); color: var(--white);
    font-size: 9.6px; font-weight: 500; line-height: 19px; text-align: center;
  }
  .rate-note {
    position: absolute; left: 31px; top: 692px; width: 265px;
    color: var(--ink); font-size: 9.8px; line-height: 12.4px;
  }
  .footer-art { position: absolute; left: 0; top: 750px; width: 612px; height: 66px; }
  .phone {
    position: absolute; left: 31px; top: 773px;
    display: flex; align-items: center; gap: 8px;
    color: var(--white); font-weight: 700; font-size: 17.5px;
  }
  .contact {
    position: absolute; top: 783px;
    display: flex; align-items: center; gap: 6px;
    color: var(--white); font-size: 9px;
  }
  .contact-email { left: 240px; }
  .contact-web { left: 404px; }
  .social { position: absolute; left: 540px; top: 781px; display: flex; gap: 6px; }
  .social-dot { width: 13px; height: 13px; border-radius: 50%; background: var(--red); }
</style>
</head>
<body>
  <main class="flyer">
    <div class="hero-band"></div>

    <svg class="hero-art" viewBox="0 0 612 360">
      <defs>
        <linearGradient id="ring" x1="0" y1="0" x2="0.4" y2="1">
          <stop offset="0" stop-color="#6a6a6a"/>
          <stop offset="1" stop-color="#2f2f2f"/>
        </linearGradient>
        <linearGradient id="photo" x1="0" y1="0" x2="1" y2="1">
          <stop offset="0" stop-color="#dfe3e5"/>
          <stop offset="0.45" stop-color="#b9b4b1"/>
          <stop offset="0.75" stop-color="#8f8a8b"/>
          <stop offset="1" stop-color="#eef1f1"/>
        </linearGradient>
      </defs>
      <ellipse cx="540" cy="66" rx="312" ry="280" fill="url(#ring)"/>
      <ellipse cx="540" cy="66" rx="304" ry="272" fill="var(--white)"/>
      <g role="img" aria-label="Photo of a smiling senior couple embracing at home">
        <ellipse cx="540" cy="66" rx="299" ry="267" fill="url(#photo)"/>
      </g>
    </svg>

    <div class="brand"><span class="brand-dot"></span>CORVANT SHIELD</div>

    <h1 class="hero-title">OUR PLANS ARE<br>BASED ON YOURS</h1>
    <p class="hero-lead">Get the right Final Expense Insurance, Medicare Supplement Insurance or Mortgage Protection Insurance plan for your family's peace-of-mind!</p>

    <section class="col-left">
      <h2 class="section-title">Final Expense Insurance</h2>
      <p>Final Expense Insurance is a type of permanent life insurance where the death benefit is used to cover (but not limited to) medical costs, funeral costs and other end-of-life expenses. It is a budget friendly option with a death benefit of up to $40k.</p>
      <h3 class="benefits-title">Benefits:</h3>
      <ul class="check-list">
        <li>All plans we offer are state regulated</li>
        <li>Relatively low monthly premiums</li>
        <li>Premiums can never increase</li>
        <li>Your policy can never be cancelled as long as you pay your premium</li>
        <li>No medical exams</li>
        <li>Guaranteed Death Benefit</li>
        <li>Many policies we offer are Guaranteed Acceptance, "Day 1" coverage, have a child/grandchild rider and/or have an accelerated death benefit rider</li>
      </ul>
    </section>

    <div class="rates">
      <div class="rate-row"><span class="rate-label">Monthly premiums as low as</span><span class="rate-value">$10</span></div>
      <div class="rate-row"><span class="rate-label">Death Benefits as high as</span><span class="rate-value">$40,000</span></div>
    </div>
    <p class="rate-note">Based on an insured that is a 65 year old, non-smoking female that has no medical conditions with death benefit of $2k</p>

    <section class="col-right">
      <h2 class="about-title">ABOUT US</h2>
      <div class="block">
        <h3 class="sub-title">We Work for You</h3>
        <p class="plain">We have been helping clients in North Idaho/<br>Eastern Washington prepare for the unknown.<br>We Also Specialize In:</p>
        <ul class="check-list right-list">
          <li>Medicare Supplement Insurance (MediGap)</li>
          <li>Annuities</li>
          <li>Final Expense</li>
        </ul>
        <p>We have access to the industry's top insurance carriers so you can get the right coverage that fits your budget.</p>
      </div>
      <div class="block">
        <h3 class="sub-title">Assessing Need</h3>
        <p>Unforeseen events and a lack of the right kind of insurance can spell trouble quickly. Contact us today, to set up a free assessment time. We will analyze your insurance needs and get you and your family the right coverage quickly at a budget friendly price.</p>
      </div>
      <div class="block">
        <h3 class="sub-title">Your Unique</h3>
        <p class="plain">Everyone has different insurance needs.<br>Find out how we can give you the peace of mind knowing your family wont have a financial burden if something were to happen to you.<br>and/or<br>Find out how we can help find the right plan to keep your medical costs manageable.</p>
      </div>
    </section>

    <svg class="footer-art" viewBox="0 0 612 66" aria-hidden="true">
      <rect x="0" y="7" width="612" height="59" fill="var(--footer)"/>
      <path d="M0 0 H196 Q227 0 227 32 V66 H0 Z" fill="var(--white)"/>
      <path d="M0 2 H194 Q224 2 224 33 V66 H0 Z" fill="var(--red)"/>
    </svg>

    <div class="phone">
      <svg width="17" height="17" viewBox="0 0 24 24" aria-hidden="true">
        <path d="M6.6 10.8a15.2 15.2 0 0 0 6.6 6.6l2.2-2.2a1 1 0 0 1 1-.25 11.4 11.4 0 0 0 3.6.57 1 1 0 0 1 1 1V20a1 1 0 0 1-1 1A17 17 0 0 1 3 4a1 1 0 0 1 1-1h3.5a1 1 0 0 1 1 1c0 1.250.2 2.450.57 3.57a1 1 0 0 1-.25 1z" fill="var(--white)"/>
      </svg>
      (208)555.0147
    </div>

    <div class="contact contact-email">
      <svg width="9" height="8" viewBox="0 0 10 8" aria-hidden="true"><rect x="0.5" y="0.5" width="9" height="7" rx="1" fill="var(--red)"/><path d="M1 1.5 5 4.5 9 1.5" stroke="var(--white)" stroke-width="1" fill="none"/></svg>
      tkelwer@corvantshield.com
    </div>
    <div class="contact contact-web">
      <svg width="9" height="9" viewBox="0 0 10 10" aria-hidden="true"><circle cx="5" cy="5" r="4.3" fill="none" stroke="var(--red)" stroke-width="1.2"/><path d="M0.8 5H9.2M5 0.8c-2.2 2.5-2.2 5.9 0 8.4M5 0.8c2.2 2.5 2.2 5.9 0 8.4" stroke="var(--red)" stroke-width="0.9" fill="none"/></svg>
      www.corvantshield.com
    </div>
    <div class="social" role="img" aria-label="Social media links">
      <span class="social-dot"></span>
      <span class="social-dot"></span>
    </div>
  </main>
</body>
</html>
```